Quill Petal Loft Hair Salon needs a Webpage design

Quill Petal Loft in Englewood is looking to start their web page, url and business emails, we want to be able to upload pictures and videos on the website. we do blow outs , makeup, color, lash extension, gel manicures

Target Market(s)

everyone

Industry/Entity Type

Beauty Salon

Coding

Coded - Design and coding required

Number of Pages Required

5+ page

Font styles to use
Serif

Colors
ffcf3e
9d9d9d
000000
ffffff

Requirements
Must have
• about us, contact us, products, menu, location, gallery, press
Nice to have
• play video gallery

```html
<!DOCTYPE html>
<html lang="en">
<head>
<meta charset="utf-8">
<title>Quill Petal Loft Hair Salon</title>
<link href="https://fonts.googleapis.com/css2?family=Lobster&family=Raleway:wght@400;600;700&family=Open+Sans:wght@400;600;700&display=swap" rel="stylesheet">
<style>
:root{
  --gold:#ffcf3e;
  --gold-deep:#f9c530;
  --gold-soft:#ffd85c;
  --grey:#9d9d9d;
  --ink:#000000;
  --text:#333333;
  --white:#ffffff;
  --night:#14202e;
}
*{box-sizing:border-box;margin:0;padding:0}
html,body{width:1200px;height:2804px;overflow:hidden}
body{font-family:"Open Sans",Arial,sans-serif;color:var(--text);background:var(--white);position:relative}
.script{font-family:"Lobster",cursive}
.abs{position:absolute}

/* header */
.site-header{position:absolute;left:0;top:0;width:1200px;height:129px;background:var(--white)}
.brand{position:absolute;left:161px;top:40px;display:flex;align-items:center;gap:10px;font-family:"Raleway",sans-serif;font-weight:700;font-size:27px;color:var(--gold)}
.brand-dot{width:16px;height:16px;border-radius:50%;background:var(--gold)}
.call{position:absolute;left:853px;top:21px;display:flex;align-items:center;gap:10px;font-family:"Raleway",sans-serif;font-size:14px;font-weight:600;color:#444}
.call-icon{width:30px;height:30px;border-radius:50%;background:var(--gold);display:flex;align-items:center;justify-content:center}
.main-nav{position:absolute;left:402px;top:84px;width:640px;display:flex;justify-content:space-between;font-family:"Raleway",sans-serif;font-size:12px;font-weight:600;color:#222;text-transform:uppercase}
.nav-notch{position:absolute;left:413px;top:121px;width:0;height:0;border-left:8px solid transparent;border-right:8px solid transparent;border-bottom:8px solid var(--gold)}

/* hero */
.hero{position:absolute;left:0;top:129px;width:1200px;height:563px;background:linear-gradient(90deg,#2b2f38 0%,#3a3f49 22%,#1d2a3a 45%,var(--night) 100%)}
.hero-photo{position:absolute;left:0;top:0;width:560px;height:563px;background:radial-gradient(ellipse at 55% 40%,#b89a8a 0%,#5a4a48 35%,rgba(30,34,44,0) 70%)}
.hero-copy{position:absolute;right:160px;top:180px;width:400px;text-align:right;color:var(--white)}
.hero-copy h1{font-family:"Lobster",cursive;font-weight:400;font-size:42px;line-height:1.1}
.hero-copy p{margin-top:14px;font-size:13.5px;font-weight:700;line-height:20px}
.btn{display:inline-flex;align-items:center;justify-content:center;font-family:"Raleway",sans-serif;font-weight:700;font-size:13px;text-transform:uppercase;color:var(--white)}
.btn-gold{background:var(--gold)}
.hero .btn{margin-top:22px;width:150px;height:38px}
.slider-dots{position:absolute;left:527px;top:507px;display:flex;gap:8px}
.slider-dots span{width:33px;height:6px;background:var(--white)}
.slider-dots .on{background:var(--gold)}

/* services */
.services{position:absolute;left:0;top:692px;width:1200px;height:303px;display:flex}
.service{flex:1;text-align:center;color:var(--white);padding-top:30px}
.service:nth-child(odd){background:var(--gold-deep)}
.service:nth-child(even){background:var(--gold)}
.service-icon{width:84px;height:84px;margin:0 auto}
.service h3{margin-top:30px;font-family:"Raleway",sans-serif;font-size:18px;font-weight:700;text-transform:uppercase;letter-spacing:.5px}
.service p{margin:12px auto 0;width:210px;font-size:10.5px;line-height:15px;opacity:.9}
.service .more{display:block;margin-top:16px;font-family:"Raleway",sans-serif;font-size:13px;font-weight:700;text-transform:uppercase}

/* welcome */
.section-title{font-family:"Lobster",cursive;font-weight:400;font-size:31px;text-align:center;color:#2a2a2a}
.welcome{position:absolute;left:0;top:995px;width:1200px;height:417px}
.welcome .section-title{position:absolute;top:36px;width:100%}
.feature{position:absolute;top:99px;width:278px}
.feature-photo{width:278px;height:170px;border-radius:3px}
.feature h3{margin-top:26px;font-family:"Raleway",sans-serif;font-size:17px;font-weight:700;text-transform:uppercase;color:#222}
.feature p{margin-top:8px;font-size:11px;line-height:15px;color:#444}

/* appointment */
.appointment{position:absolute;left:0;top:1412px;width:1200px;height:387px;background:radial-gradient(ellipse at 50% 30%,#4a3a30 0%,#2a221c 55%,#1a1613 100%);text-align:center;color:var(--white)}
.appointment h2{margin-top:80px;font-family:"Lobster",cursive;font-weight:400;font-size:30px}
.appointment h2 em{font-style:normal;color:var(--gold)}
.appointment p{margin:28px auto 0;width:820px;font-size:11px;line-height:19px}
.appointment .actions{margin-top:32px;display:flex;justify-content:center;gap:9px}
.appointment .btn{width:200px;height:51px}
.btn-outline{border:2px solid var(--white)}

/* gallery */
.gallery{position:absolute;left:0;top:1799px;width:1200px;height:604px}
.gallery .section-title{position:absolute;top:28px;width:100%}
.gallery .lead{position:absolute;top:72px;left:210px;width:780px;text-align:center;font-size:11px;line-height:19px;color:#444}
.tile{position:absolute}
.tile-hover{background:rgba(255,207,62,.92);display:flex;align-items:center;justify-content:center;gap:8px}
.tile-hover span{width:34px;height:34px;border-radius:50%;background:var(--gold-deep);box-shadow:0 0 0 2px rgba(255,255,255,.35);display:flex;align-items:center;justify-content:center}

/* contact */
.contact{position:absolute;left:0;top:2403px;width:1200px;height:342px;background:linear-gradient(180deg,#0d0d0d,#000);color:var(--white)}
.contact .section-title{color:var(--white);position:absolute;top:30px;width:100%}
.contact .lead{position:absolute;top:82px;left:220px;width:760px;text-align:center;font-size:11px;line-height:19px}
.field{position:absolute;left:161px;width:312px;height:35px;background:var(--white);color:#999;font-size:11px;font-style:italic;padding:10px 8px}
.message{position:absolute;left:484px;top:144px;width:346px;height:106px;background:var(--white);color:#999;font-size:11px;font-style:italic;padding:10px 8px}
.submit{position:absolute;left:161px;top:267px;width:312px;height:35px;background:var(--gold);font-family:"Raleway",sans-serif;font-weight:700;font-size:12px;text-transform:uppercase;color:var(--white);display:flex;align-items:center;justify-content:center;gap:6px}
.locations{position:absolute;left:875px;top:142px;width:170px;list-style:none;font-size:10.5px;line-height:15px}
.locations li{position:relative;padding-left:16px;margin-bottom:10px}
.locations svg{position:absolute;left:0;top:2px}

/* footer */
.site-footer{position:absolute;left:0;top:2745px;width:1200px;height:59px;background:var(--gold);color:var(--white)}
.site-footer small{position:absolute;left:161px;top:22px;font-size:10px}
.social{position:absolute;left:925px;top:17px;display:flex;gap:8px}
.social span{width:24px;height:24px;border-radius:50%;border:1.5px solid var(--white)}
</style>
</head>
<body>

<header class="site-header">
  <div class="brand"><span class="brand-dot"></span>Quill Petal Loft</div>
  <div class="call">
    <span class="call-icon"><svg width="14" height="14" viewBox="0 0 24 24"><path fill="#fff" d="M6.6 10.8a15.1 15.1 0 0 0 6.6 6.6l2.2-2.2c.3-.3.7-.4 1-.2 1.1.4 2.3.6 3.6.6.6 0 1 .4 1 1V20c0 .6-.4 1-1 1A17 17 0 0 1 3 4c0-.6.4-1 1-1h3.5c.6 0 1 .4 1 1 0 1.3.2 2.5.6 3.6.1.3 0 .7-.2 1z"/></svg></span>
    CALL US: 555-014-2290
  </div>
  <nav class="main-nav">
    <span>Home</span><span>About</span><span>Menus</span><span>Products</span><span>Locations</span><span>Press</span><span>Book Now / Contact</span><span>Social</span>
  </nav>
  <div class="nav-notch"></div>
</header>

<section class="hero">
  <div class="hero-photo" role="img" aria-label="Salon model with glossy straight dark hair in profile"></div>
  <div class="hero-copy">
    <h1>Quill Petal Loft</h1>
    <p>At vero eos et accusamus et iusto odio dignis simos duci mui blanditiis praesentium volu ptatum deleniti atquesui bland itiis praesentium volrrupti quos dolor.</p>
    <span class="btn btn-gold">Read More Info</span>
  </div>
  <div class="slider-dots"><span></span><span></span><span class="on"></span><span></span></div>
</section>

<section class="services">
  <div class="service">
    <div class="service-icon" role="img" aria-label="Hair spa icon"><svg width="84" height="84"><circle cx="42" cy="42" r="38" fill="none" stroke="#fff" stroke-width="3"/></svg></div>
    <h3>Hair Spa</h3>
    <p>At vero eos et accusamus et iusto odio dignis mos ducimus qui blanditiis praesentium volu ptatum deleniti atque corrupti quos dolo.</p>
    <span class="more">Read More</span>
  </div>
  <div class="service">
    <div class="service-icon" role="img" aria-label="Makeup compact icon"><svg width="84" height="84"><circle cx="42" cy="46" r="30" fill="none" stroke="#fff" stroke-width="3"/><circle cx="42" cy="46" r="20" fill="#fff"/></svg></div>
    <h3>Makeup</h3>
    <p>At vero eos et accusamus et iusto odio dignis mos ducimus qui blanditiis praesentium volu ptatum deleniti atque corrupti quos dolo.</p>
    <span class="more">Read More</span>
  </div>
  <div class="service">
    <div class="service-icon" role="img" aria-label="Waxing treatment icon"><svg width="84" height="84"><rect x="16" y="36" width="52" height="36" rx="6" fill="#fff"/></svg></div>
    <h3>Waxing</h3>
    <p>At vero eos et accusamus et iusto odio dignis mos ducimus qui blanditiis praesentium volu ptatum deleniti atque corrupti quos dolo.</p>
    <span class="more">Read More</span>
  </div>
  <div class="service">
    <div class="service-icon" role="img" aria-label="Spa stones icon"><svg width="84" height="84"><ellipse cx="54" cy="30" rx="12" ry="7" fill="#fff"/><ellipse cx="54" cy="48" rx="17" ry="8" fill="#fff"/><ellipse cx="54" cy="68" rx="22" ry="9" fill="#fff"/></svg></div>
    <h3>Manhasset</h3>
    <p>At vero eos et accusamus et iusto odio dignis mos ducimus qui blanditiis praesentium volu ptatum deleniti atque corrupti quos dolo.</p>
    <span class="more">Read More</span>
  </div>
</section>

<section class="welcome">
  <h2 class="section-title">Welcome to Quill Petal Loft</h2>
  <article class="feature" style="left:161px">
    <div class="feature-photo" role="img" aria-label="Group of guests relaxing in the salon" style="background:linear-gradient(135deg,#6b6f78,#c9b8a8 55%,#4b4e55)"></div>
    <h3>Sit Back and Relax</h3>
    <p>At vero eos et accusamus et iusto odio dignissimos ducimus qui blanditiis praesentium voluptatum deleniti atque corrupti quos dolores et quas molestias.</p>
  </article>
  <article class="feature" style="left:462px">
    <div class="feature-photo" role="img" aria-label="Guest standing beside the salon sign" style="background:linear-gradient(135deg,#3a2a20,#a07a5a 50%,#d19a40)"></div>
    <h3>The Hamptons</h3>
    <p>At vero eos et accusamus et iusto odio dignissimos ducimus qui blanditiis praesentium voluptatum deleniti atque corrupti quos dolores et quas molestias.</p>
  </article>
  <article class="feature" style="left:762px">
    <div class="feature-photo" role="img" aria-label="Two friends laughing at the bar" style="background:linear-gradient(135deg,#e9e2d6,#d9b89a 50%,#6aa8a8)"></div>
    <h3>Our Bar</h3>
    <p>At vero eos et accusamus et iusto odio dignissimos ducimus qui blanditiis praesentium voluptatum deleniti atque corrupti quos dolores et quas molestias.</p>
  </article>
</section>

<section class="appointment" role="img" aria-label="Dim spa interior background">
  <h2><em>Book an appointment</em> Open 7 days a week</h2>
  <p>QUILL PETAL LOFT is a specialized salon designed for blowouts, cuts, keratin treatments, and makeup. The shops feature state of the art facilities, custom servicing anyone who wants to enjoy great looking hair! Quill Petal Loft offers affordable luxury at its finest. Visit us before or after work, get in and out before dinner, or stay and hang as long as you want! Sed ut perspiciatis unde omnis iste natus error sit voluptatem accusantium doloremque laudantium, totam rem aperiam, eaque ipsa quae ab illo inve veritatis et quasi architecto beatae vitae dicta sunt explicabo.emo enim ipsam voluptatem quia voluptas sit aspernatur aut odit aut fugit.</p>
  <div class="actions">
    <span class="btn btn-outline">Read More Info</span>
    <span class="btn btn-gold">Book an Appointment</span>
  </div>
</section>

<section class="gallery">
  <h2 class="section-title">Our Gallery</h2>
  <p class="lead">Sed ut perspiciatis unde omnis iste natus error sit voluptatem accusantium doloremque laudantium, totam rem aperiam, eaque ipsa quae ab illo inve ntore veritatis et quasi architecto beatae vitae dicta sunt explicabo.emo enim ipsam voluptatem quia voluptas sit aspernatur aut odit aut fugit.</p>
  <div class="tile" role="img" aria-label="Portrait of model with auburn curls" style="left:161px;top:134px;width:278px;height:418px;background:linear-gradient(160deg,#5a3a2a,#a8705a 50%,#3a2418)"></div>
  <div class="tile tile-hover" style="left:451px;top:134px;width:189px;height:201px" role="img" aria-label="Makeup portrait with highlight overlay">
    <span><svg width="14" height="14" viewBox="0 0 24 24"><circle cx="10" cy="10" r="6" fill="none" stroke="#fff" stroke-width="2.5"/><path d="M15 15l5 5" stroke="#fff" stroke-width="2.5"/></svg></span>
    <span><svg width="14" height="14" viewBox="0 0 24 24"><path d="M9 15l6-6M7 11l-2 2a3.5 3.5 0 0 0 5 5l2-2M17 13l2-2a3.5 3.5 0 0 0-5-5l-2 2" fill="none" stroke="#fff" stroke-width="2.2"/></svg></span>
  </div>
  <div class="tile" role="img" aria-label="Manicured hands with pink petals" style="left:651px;top:134px;width:187px;height:201px;background:linear-gradient(150deg,#f7e1e6,#e88aa8 60%,#f5c9d6)"></div>
  <div class="tile" role="img" aria-label="Guest receiving a relaxing spa treatment" style="left:851px;top:134px;width:187px;height:201px;background:linear-gradient(150deg,#6b6a58,#c6a48a 55%,#4a4334)"></div>
  <div class="tile" role="img" aria-label="Skincare portrait with towel wrap" style="left:451px;top:350px;width:189px;height:202px;background:linear-gradient(150deg,#fbf3ec,#e8c7b0 60%,#f6ece4)"></div>
  <div class="tile" role="img" aria-label="Model with voluminous dark hair" style="left:651px;top:350px;width:387px;height:202px;background:linear-gradient(120deg,#1c1c1c,#6a625c 55%,#2a2a2a)"></div>
</section>

<section class="contact">
  <h2 class="section-title">Contact Us</h2>
  <p class="lead">Sed ut perspiciatis unde omnis iste natus error sit voluptatem accusantium doloremque laudantium, totam rem aperiam, eaque ipsa quae ab illo inve ntore veritatis et quasi architecto beatae vitae dicta sunt explicabo.emo enim ipsam voluptatem quia voluptas sit aspernatur aut odit aut fugit.</p>
  <div class="field" style="top:144px">Name:</div>
  <div class="field" style="top:185px">Phone:</div>
  <div class="field" style="top:226px">Email:</div>
  <div class="message">Message:</div>
  <div class="submit">Submit <svg width="11" height="11" viewBox="0 0 24 24"><circle cx="12" cy="12" r="11" fill="#fff"/><path d="M10 7l5 5-5 5" fill="none" stroke="#ffcf3e" stroke-width="3"/></svg></div>
  <ul class="locations">
    <li><svg width="8" height="11" viewBox="0 0 8 11"><path d="M4 0a4 4 0 0 0-4 4c0 3 4 7 4 7s4-4 4-7a4 4 0 0 0-4-4z" fill="#fff"/></svg>12 Linden Court, East Hampton, NY 555.310.4402</li>
    <li><svg width="8" height="11" viewBox="0 0 8 11"><path d="M4 0a4 4 0 0 0-4 4c0 3 4 7 4 7s4-4 4-7a4 4 0 0 0-4-4z" fill="#fff"/></svg>840 Harbor Lane, Bridgehampton, NY 555.310.7715</li>
    <li><svg width="8" height="11" viewBox="0 0 8 11"><path d="M4 0a4 4 0 0 0-4 4c0 3 4 7 4 7s4-4 4-7a4 4 0 0 0-4-4z" fill="#fff"/></svg>215 Orchard Rd, Manhasset, NY 555.310.2238</li>
    <li><svg width="8" height="11" viewBox="0 0 8 11"><path d="M4 0a4 4 0 0 0-4 4c0 3 4 7 4 7s4-4 4-7a4 4 0 0 0-4-4z" fill="#fff"/></svg>COMING SOON Englewood, NJ 555.310.LOFT</li>
  </ul>
</section>

<footer class="site-footer">
  <small>© 2014 QuillPetalLoft. All copyrights are reserved. Term of Use</small>
  <div class="social"><span></span><span></span><span></span><span></span></div>
</footer>

</body>
</html>
```